Tri-Fold Brochure for Christian Author and Speaker

Lorna Whitfield is an inspirational author and speaker, sharing her testimony and encouraging others in their walk with Christ. A gifted writer, her work has been featured on Gently Radiant, Steadfast Mornings, and Hymns & Teacups Magazine (Fall 2011).

Lorna ‘s first book, Leaving the Lantern Room: Unmasking Hidden Snares in Ordinary Living, is an informative memoir and Bible study, recounting her journey from committed Christian to witch, medium, and ghost hunter for eight years until restored to faith in Jesus Christ. She was a contributing author to Walking Past the Shadows: A Candid View of Sorcery from Those Who Left by Dale Pennington and a consultant for the novel The Keeper of Marlow Hollow by Beacon Prize Winning Author, Helen Osgood.

Lorna’s second book, An Insider’s Guide to Spiritual Warfare: 20 Battle-Tested Strategies from Behind Enemy Lines, will be published by Harvest Lane Press for Fall 2014.

Lorna is a wife and mother. She enjoys writing, spending time with her family, taking long walks, listening to music of all kinds, and experiencing God’s daily gift called life.

You can read more about Lorna and see the look and feel we are going for at www.lornawhitfield.example

The brochure is to be used as a promotional tool to gain Lorna speaking engagements. You can see the topics she covers at http://www.lornawhitfield.example/speaking-engagements/.

More info can be found at: https://www.facebook.com/AuthorLornaWhitfield
https://www.facebook.com/VMUCX
https://www.facebook.com/LeavingtheLanternRoom
https://www.facebook.com/OpenDoorOutreach
http://www.opendooroutreach.example

I have uploaded 3 headshots, book covers for both of Lorna's books and the design layout in .EPS format from Swiftprintery.example where I will be getting printing done.

3 more days till the contest ends get your final designs in.

Reason: I'm extending this as I am tied up at a leadership conference and will not be able to give this the attention it deserves till the weekend.

Target Market(s)

Churches and women's groups. Lorna's current audience skews heavy to women on a 70/30 ratio.

Industry/Entity Type

Christian

Requirements
Must have
• Headshot I have uploaded 3
Quotes from previous speaking engagements you can find those at http://www.lornawhitfield.example/speaking-engagements/

```html
<!DOCTYPE html>
<html lang="en">
<head>
<meta charset="utf-8">
<title>Lorna Whitfield – Tri-Fold Brochure</title>
<link rel="stylesheet" href="https://fonts.googleapis.com/css2?family=Cinzel:wght@400;500&family=Didact+Gothic&family=Nunito:wght@400;800;900&display=swap">
<style>
  :root{
    --crimson:#c2205a;
    --crimson-deep:#9e1646;
    --maroon:#7d0f36;
    --ink:#6e6a6b;
    --blush:#fbe9ee;
    --blush-soft:#fdf4f6;
    --white:#ffffff;
  }
  *{margin:0;padding:0;box-sizing:border-box}
  html,body{width:1200px;height:848px;overflow:hidden;background:#fff}
  .brochure{position:relative;width:1200px;height:848px;display:flex;overflow:hidden}
  .panel{position:relative;height:848px;overflow:hidden}

  /* Speaking panel */
  .panel-speaking{width:399px;background:linear-gradient(160deg,var(--blush) 0%,var(--blush-soft) 40%,#fff 75%)}
  .speaking-intro{position:absolute;left:28px;top:31px;width:345px;font-family:"Didact Gothic",sans-serif;font-size:15px;line-height:24px;color:var(--ink);text-align:justify}
  .tab-heading{float:left;margin:0 14px 6px -28px;padding:4px 18px 6px 28px;background:var(--crimson);color:var(--white);font-family:"Nunito",sans-serif;font-weight:400;font-size:40px;line-height:48px;border-radius:0 26px 0 26px}
  .accent{color:var(--crimson)}
  .topics{position:absolute;left:34px;top:362px;width:330px;font-family:"Didact Gothic",sans-serif}
  .topics h3{font-family:"Nunito",sans-serif;font-weight:800;font-size:18px;color:var(--crimson);margin-bottom:6px}
  .topics ul{list-style:none}
  .topics li{position:relative;padding-left:22px;font-size:16px;line-height:24px;color:var(--crimson-deep)}
  .topics li::before{content:"";position:absolute;left:3px;top:9px;width:8px;height:8px;background:var(--crimson)}
  .panel-art{position:absolute;left:0;top:0;width:100%;height:100%}

  /* Testimony panel */
  .panel-testimony{width:399px;background:var(--crimson)}
  .testimony-heading{position:absolute;left:45px;top:52px;font-family:"Nunito",sans-serif;font-weight:900;font-size:32px;color:var(--white)}
  .testimony-copy{position:absolute;left:45px;top:100px;width:299px;font-family:"Didact Gothic",sans-serif;font-size:15px;line-height:26px;color:var(--white);text-align:justify}
  .testimony-copy strong{font-family:"Nunito",sans-serif;font-weight:800}
  .portrait-frame{position:absolute;left:127px;top:494px;width:146px;height:218px;border:4px solid var(--white);background:linear-gradient(160deg,#5d5a3e 0%,#6b5446 45%,#3a2a2a 100%)}
  .signature{position:absolute;left:0;top:724px;width:100%;text-align:center;color:var(--white)}
  .signature .name{font-family:"Cinzel",serif;font-size:20px;line-height:26px;letter-spacing:1px}
  .signature .url{font-family:"Didact Gothic",sans-serif;font-size:15px;margin-top:4px}

  /* Cover panel */
  .panel-cover{width:402px;background:linear-gradient(180deg,#fff 0%,var(--blush-soft) 55%,var(--blush) 100%)}
  .cover-title{position:absolute;left:0;top:36px;width:100%;text-align:center;font-family:"Cinzel",serif;color:var(--crimson-deep)}
  .cover-title .name{font-size:46px;line-height:48px;letter-spacing:1px}
  .cover-title .role{font-size:22px;margin-top:8px;letter-spacing:1px}
  .tagline{position:absolute;left:0;top:666px;width:100%;font-family:"Nunito",sans-serif;color:var(--crimson)}
  .tagline p{font-size:30px;line-height:29px;font-weight:400}
  .tagline b{font-weight:900}
  .tagline .lead{color:var(--maroon);font-weight:900;font-size:34px;line-height:36px;padding-left:28px}
  .tagline .l2{padding-left:42px}
  .tagline .l3{padding-left:60px;font-weight:900}
  .tagline .l4{padding-left:100px}
</style>
</head>
<body>
<main class="brochure">

  <section class="panel panel-speaking">
    <svg class="panel-art" viewBox="0 0 399 848" aria-hidden="false">
      <defs>
        <linearGradient id="speakPhoto" x1="0" y1="0" x2="1" y2="1">
          <stop offset="0" stop-color="#8a4a48"/>
          <stop offset="0.5" stop-color="#a86a5c"/>
          <stop offset="1" stop-color="#5a2f2c"/>
        </linearGradient>
      </defs>
      <path role="img" aria-label="Headshot of Lorna Whitfield in front of a red wooden wall" d="M0 640 C120 625 260 590 399 570 L399 848 L0 848 Z" fill="url(#speakPhoto)"/>
      <path d="M0 640 C120 625 260 590 399 570" fill="none" stroke="var(--crimson)" stroke-width="10"/>
    </svg>
    <div class="speaking-intro">
      <h2 class="tab-heading">Speaking</h2>
      As a speaker, <span class="accent">Lorna Whitfield</span> shares from her own life lessons and as a Biblical Counselor, encouraging others toward a deeper walk with God. Lorna offers sound, heartfelt, and practical biblical advice on issues relevant to the <span class="accent">21st Century Christian</span>. read more.....
    </div>
    <div class="topics">
      <h3>Speaking Topics Include:</h3>
      <ul>
        <li>Christians and the Occult</li>
        <li>Homelessness (with Glen Whitfield)</li>
        <li>Human Trafficking</li>
        <li>Marriage Restoration (with Glen Whitfield)</li>
        <li>Prayer as a Lifestyle</li>
        <li>Spiritual Warfare</li>
      </ul>
    </div>
  </section>

  <section class="panel panel-testimony">
    <h2 class="testimony-heading">Testimony</h2>
    <p class="testimony-copy">I was raised in a traditional <strong>Christian home</strong>. One of my earliest memories of church is sitting on a hard wooden pew with my mother listening to a pipe organ play a traditional hymn. We were attending a Methodist church at the time. I remember hearing Bible stories, singing songs about the B.I.B.L.E and Jesus Loving the Little Children. It wasn’t until I was six years old attending Vacation Bible School that I learned how Jesus wanted to save me from my sins. Read more....</p>
    <div class="portrait-frame" role="img" aria-label="Portrait of Lorna Whitfield leaning against a tree, arms crossed"></div>
    <div class="signature">
      <div class="name">Lorna<br>Whitfield</div>
      <div class="url">www.lornawhitfield.example</div>
    </div>
  </section>

  <section class="panel panel-cover">
    <div class="cover-title">
      <div class="name">Lorna<br>Whitfield</div>
      <div class="role">Author | Speaker</div>
    </div>
    <svg class="panel-art" viewBox="0 0 402 848">
      <defs>
        <linearGradient id="coverPhoto" x1="0" y1="0" x2="1" y2="1">
          <stop offset="0" stop-color="#6f7a4e"/>
          <stop offset="0.45" stop-color="#8c5a4a"/>
          <stop offset="1" stop-color="#5a3a2e"/>
        </linearGradient>
      </defs>
      <path role="img" aria-label="Portrait of Lorna Whitfield smiling in a garden" d="M0 252 C120 232 280 212 402 206 L402 566 C300 570 160 578 0 596 Z" fill="url(#coverPhoto)"/>
      <path d="M0 252 C120 232 280 212 402 206" fill="none" stroke="var(--crimson)" stroke-width="8"/>
      <path d="M0 596 C160 578 300 570 402 566" fill="none" stroke="var(--crimson)" stroke-width="8"/>
    </svg>
    <div class="tagline">
      <p class="lead">Lorna Whitfield</p>
      <p class="l2">is an <b>Inspirational</b></p>
      <p class="l3">Author</p>
      <p class="l4">and <b>Speaker</b></p>
    </div>
  </section>

</main>
</body>
</html>
```